Brand and Marketing Coach Needs PDF Designed

I have content that i need placed into a simple but great PDF design. The PDF is about the formula I use to build personal brands. This is geared towards entrepreneurs, experts, coaches, therapists, wellness practitioners, and indpendent business owners who serve to improve the lives of others.
The company name is changing from TorvelCast to Selling with the Village (I don't have that logo yet, so working backwards a bit. For now, the TorvelCast logo can be used.) My brand is NOT formal and corporate, but it's also not neon-pink and screaming at you. It's down to earth, hip, a bit modern but warm. It's about no BS and authenticity. The final deliverable should make the reader feel focused, smart, motivated and hopeful.

Target Market(s)

Conscious entrepreneurs and small business owners. this one is specifically for pharmacy entrepreneurs but this will be used for various audiences later.

Font styles to use
Sans Serif

Colors
eaf1f7
3377b5
6b449b
f37122
faa54b
f68e4e
ffc214

Requirements
Must have
• Modern design. colors that match logo - 4e5583 (i think that is the blue.) d65a40.
• Could have these colors as well: c6a254, 01bcc3
• But open to other colors
Nice to have
• I'd like to see some ways to make this PDF simple and readable, and eye-catching. I'd also like to use the uploaded ebooks for design ideas.
Should not have
• neon colors, clip art

```html
<!DOCTYPE html>
<html lang="en">
<head>
<meta charset="utf-8">
<title>About Me – TorvelCast</title>
<link rel="stylesheet" href="https://fonts.googleapis.com/css2?family=EB+Garamond:ital,wght@0,400;0,600;0,700;1,400;1,700&display=swap">
<style>
  :root {
    --stage: #000000;
    --card: #4f5682;
    --ink: #ffffff;
    --frame: #ffffff;
    --photo-top: #7a5a4c;
    --photo-mid: #c0603a;
    --photo-low: #2d2f3b;
  }
  * { margin: 0; padding: 0; box-sizing: border-box; }
  html, body {
    width: 1141px; height: 1200px; overflow: hidden;
    background: var(--stage);
  }
  .stage { position: relative; width: 1141px; height: 1200px; }
  .about-card {
    position: absolute; left: 115px; top: 71px;
    width: 910px; height: 703px;
    background: var(--card);
    color: var(--ink);
    font-family: "EB Garamond", Georgia, serif;
  }
  .portrait {
    position: absolute; left: 84px; top: 63px;
    width: 222px; height: 350px;
    border: 2px solid var(--frame);
    background: linear-gradient(160deg, var(--photo-top) 0%, var(--photo-mid) 40%, var(--photo-low) 100%);
  }
  .heading {
    position: absolute; left: 339px; top: 60px;
    font-size: 23px; font-weight: 600; letter-spacing: 0.5px;
  }
  .copy {
    position: absolute; font-size: 16.6px; line-height: 19.2px;
  }
  .copy strong { font-weight: 700; }
  .copy.narrow { left: 339px; width: 520px; }
  .copy.wide { left: 84px; width: 800px; }
  .connect-label {
    position: absolute; left: 354px; top: 600px;
    font-size: 23px; font-style: italic; font-weight: 700;
  }
  .contact-list { position: absolute; left: 580px; top: 560px; list-style: none; }
  .contact-list li {
    display: flex; align-items: center; height: 28px; margin-bottom: 10px;
    font-size: 16.6px;
  }
  .contact-list svg { width: 28px; height: 28px; margin-right: 10px; flex: none; }
  .caption {
    position: absolute; left: 0; width: 1141px; text-align: center;
    color: var(--ink);
    font-family: Arial, Helvetica, sans-serif; font-size: 46px;
  }
</style>
</head>
<body>
<div class="stage">
  <section class="about-card">
    <div class="portrait" role="img" aria-label="Portrait photo of Dana Whitlock holding a laptop"></div>

    <h1 class="heading">ABOUT ME</h1>

    <p class="copy narrow" style="top:103px">I’m <strong>Dana Whitlock</strong>, Founder, and CEO of <strong>TorvelCast</strong> and<br><em>Selling with the Village.</em></p>

    <p class="copy narrow" style="top:163px"><strong>As a marketing strategist and coach,</strong> I help conscious startup and<br>small biz owners to create a unique and compelling brand and<br>stand-out content to grow their business online... so they can be<br>proud of the positive impact they are able to make in the world.</p>

    <p class="copy narrow" style="top:260px"><strong>I believe</strong> that you can reach your goals, get people talking about your<br>message, and have a unique brand that magnetically attracts the right<br>clients…&nbsp; You just need the strategy and tools to make your vision<br>come to life.</p>

    <p class="copy narrow" style="top:356px"><strong>I've worn several hats</strong> in my marketing career, from copywriter to PR<br>pro to director and co-creator of big visions. You name it – I've<br>probably done it.</p>

    <p class="copy wide" style="top:435px"><strong>When I walked away from my job</strong> as a marketing director to start my own business, I never looked back.<br>It was one of the most frightening, yet most empowering things I have ever done.</p>

    <p class="copy wide" style="top:493px"><strong>The real reason I created my business</strong> was to do what I love and work with people in whom I believe.</p>

    <p class="connect-label">Connect with me:</p>
    <ul class="contact-list">
      <li><svg viewBox="0 0 28 28" aria-hidden="true"><circle cx="14" cy="14" r="14" fill="#fff"/></svg>www.linkhive.net/torvelcast</li>
      <li><svg viewBox="0 0 28 28" aria-hidden="true"><circle cx="14" cy="14" r="14" fill="#fff"/></svg>www.snapgallery.net/torvelcast</li>
      <li><svg viewBox="0 0 28 28" aria-hidden="true"><circle cx="14" cy="14" r="14" fill="#fff"/><rect x="7" y="9" width="14" height="10" fill="none" stroke="#4f5682" stroke-width="1.8"/><path d="M7 9 L14 15 L21 9" fill="none" stroke="#4f5682" stroke-width="1.8"/></svg>dana@torvelcast.com</li>
    </ul>
  </section>

  <p class="caption" style="top:858px">This would be our last page, am I right?</p>
  <p class="caption" style="top:948px">17 pages in TOTAL</p>
</div>
</body>
</html>
```